Real Estate Business Card

On the front side I want to have my info, my brokerage info.
On the back side I want have my complany’s logo, website and Facebook link. I will provide all this once I select a design.

I would like to see Black background and gold text, Dark Blue and gold text and White and blue text designs

Font styles to use
Sans Serif
Script

```html
<!DOCTYPE html>
<html lang="en">
<head>
<meta charset="UTF-8">
<title>Northvale Real Estate – Business Card</title>
<link rel="stylesheet" href="https://fonts.googleapis.com/css2?family=Montserrat:wght@600;700;800&family=Roboto:wght@400;500;700&display=swap">
<style>
  :root {
    --backdrop: #2b2b2d;
    --card: #1f1f21;
    --card-edge: #2a2a2c;
    --gold: #f2c744;
    --red: #e0383e;
    --steel: #5b6577;
    --steel-soft: rgba(91, 101, 119, 0.55);
    --white: #f4f4f4;
    --divider: #8a8d94;
  }
  * { box-sizing: border-box; margin: 0; padding: 0; }
  html, body {
    width: 1200px; height: 900px; overflow: hidden;
    background: var(--backdrop);
  }
  .canvas {
    position: relative; width: 1200px; height: 900px;
    display: flex; flex-direction: column; align-items: center; justify-content: center; gap: 40px;
  }
  .card {
    position: relative; width: 700px; height: 390px;
    background: var(--card);
    border: 1px solid var(--card-edge);
    overflow: hidden;
  }

  /* Back side */
  .card-back {
    display: flex; flex-direction: column; align-items: center; justify-content: center;
  }
  .back-mark {
    display: flex; align-items: center; gap: 18px;
  }
  .back-mark .brand-square {
    width: 34px; height: 34px; background: var(--steel-soft);
  }
  .back-name {
    font-family: "Montserrat", sans-serif; font-weight: 800;
    font-size: 64px; letter-spacing: 1px; color: var(--steel-soft);
    text-transform: uppercase;
  }
  .back-tag {
    margin-top: 6px;
    font-family: "Montserrat", sans-serif; font-weight: 800;
    font-size: 20px; letter-spacing: 14px; color: var(--steel-soft);
    text-transform: uppercase;
  }

  /* Front side */
  .card-front { display: flex; }
  .brand-block {
    width: 390px; height: 335px;
    display: flex; flex-direction: column; align-items: center; justify-content: center;
  }
  .brand-row { display: flex; align-items: center; gap: 12px; }
  .brand-row .brand-square { width: 26px; height: 26px; background: var(--steel); }
  .brand-name {
    font-family: "Montserrat", sans-serif; font-weight: 800;
    font-size: 44px; color: var(--steel); text-transform: uppercase;
  }
  .brand-tag {
    margin-top: 4px;
    font-family: "Montserrat", sans-serif; font-weight: 800;
    font-size: 14px; letter-spacing: 10px; color: var(--steel); text-transform: uppercase;
  }
  .divider {
    position: absolute; left: 392px; top: 14px; width: 2px; height: 272px;
    background: linear-gradient(to bottom, transparent, var(--divider) 20%, var(--divider) 80%, transparent);
  }
  .contact {
    position: absolute; left: 420px; top: 38px;
    font-family: "Roboto", sans-serif; color: var(--white);
  }
  .person-name {
    font-family: "Montserrat", sans-serif; font-weight: 700;
    font-size: 24px; color: var(--gold); letter-spacing: 0.5px;
  }
  .person-title {
    font-family: "Montserrat", sans-serif; font-weight: 700;
    font-size: 15px; color: var(--red); margin-top: -2px;
  }
  .address { margin-top: 14px; font-size: 17px; line-height: 21px; }
  .contact-list { list-style: none; margin-top: 12px; }
  .contact-list li {
    display: flex; align-items: center; gap: 10px;
    font-size: 18px; line-height: 24px;
  }
  .contact-list svg { width: 16px; height: 16px; flex: none; fill: var(--gold); }
  .band-line {
    position: absolute; left: 0; right: 0; bottom: 36px; height: 5px; background: var(--steel);
  }
  .band-red {
    position: absolute; left: 0; right: 0; bottom: 0; height: 34px; background: var(--red);
  }
</style>
</head>
<body>
<main class="canvas">

  <section class="card card-back" aria-label="Back of card">
    <div class="back-mark">
      <span class="brand-square"></span>
      <span class="back-name">Northvale</span>
    </div>
    <div class="back-tag">Real Estate</div>
  </section>

  <section class="card card-front" aria-label="Front of card">
    <div class="brand-block">
      <div class="brand-row">
        <span class="brand-square"></span>
        <span class="brand-name">Northvale</span>
      </div>
      <div class="brand-tag">Real Estate</div>
    </div>

    <div class="divider"></div>

    <div class="contact">
      <h1 class="person-name">DANIEL REYES</h1>
      <p class="person-title">CEO/FOUNDER</p>
      <p class="address">2140 Harbor View Road<br>Juneau, Alaska 99801</p>
      <ul class="contact-list">
        <li>
          <svg viewBox="0 0 24 24" aria-hidden="true"><path d="M6.6 10.8a15.1 15.1 0 0 0 6.6 6.6l2.2-2.2c.3-.3.7-.4 1-.2 1.1.4 2.3.6 3.6.6.6 0 1 .4 1 1V20c0 .6-.4 1-1 1A17 17 0 0 1 3 4c0-.6.4-1 1-1h3.5c.6 0 1 .4 1 1 0 1.3.2 2.5.6 3.6.1.3 0 .7-.2 1z"/></svg>
          907 555 0142
        </li>
        <li>
          <svg viewBox="0 0 24 24" aria-hidden="true"><path d="M7 1h10a2 2 0 0 1 2 2v18a2 2 0 0 1-2 2H7a2 2 0 0 1-2-2V3a2 2 0 0 1 2-2zm0 3v14h10V4zm5 15.5a1 1 0 1 0 0 2 1 1 0 0 0 0-2z"/></svg>
          907 555 0187
        </li>
        <li>
          <svg viewBox="0 0 24 24" aria-hidden="true"><path d="M6 2h12v5H6zM4 8h16a2 2 0 0 1 2 2v7h-4v5H6v-5H2v-7a2 2 0 0 1 2-2zm4 7v5h8v-5z"/></svg>
          907 555 0123
        </li>
        <li>
          <svg viewBox="0 0 24 24" aria-hidden="true"><path d="M2 5h20v14H2zm2 2v.5l8 5 8-5V7zm0 2.8V17h16V9.8l-8 5z"/></svg>
          daniel@northvale.com
        </li>
        <li>
          <svg viewBox="0 0 24 24" aria-hidden="true"><path d="M12 2a10 10 0 1 0 0 20 10 10 0 0 0 0-20zm-1 17.9A8 8 0 0 1 4.1 11H8c.1 3 1.2 6.3 3 8.9zM4.1 9A8 8 0 0 1 11 4.1C9.2 6.7 8.1 9 8 9zm8.9 10.9c1.8-2.6 2.9-5.9 3-8.9h3.9a8 8 0 0 1-6.9 8.9zM16 9c-.1 0-1.2-2.3-3-4.9A8 8 0 0 1 19.9 9z"/></svg>
          www.northvale.com
        </li>
      </ul>
    </div>

    <div class="band-line"></div>
    <div class="band-red"></div>
  </section>

</main>
</body>
</html>
```